We need professional looking business cards for our e-assessment business based in Europe. Our company is called Velmo.

You can just use sample name and addresses.

The colours we use are:

#70abe4 (blue)
#FF6600 (orange)

The back side should say: E-assessment made easy

This is the print-shop we are using. Please look at the link for info about formats: http://nl.prindavo.com/help/faq/using-my-own-artwork.html

Target market is education and large corporations

Business

```html
<!DOCTYPE html>
<html lang="en">
<head>
<meta charset="utf-8">
<title>Velmo business cards</title>
<link href="https://fonts.googleapis.com/css2?family=Barlow:wght@400;500&display=swap" rel="stylesheet">
<style>
  :root {
    --backdrop: #e8e8ea;
    --card: #fbfbfb;
    --orange: #e65c00;
    --blue: #70abe4;
    --ink: #2f2f31;
    --ink-soft: #3c3c3e;
  }
  html, body {
    margin: 0;
    width: 1200px;
    height: 800px;
    overflow: hidden;
    background: var(--backdrop);
    font-family: "Barlow", Arial, sans-serif;
  }
  .stage {
    position: relative;
    width: 1200px;
    height: 800px;
  }
  .card {
    position: absolute;
    background: var(--card);
    box-shadow: 0 0 0 1px rgba(0,0,0,0.04);
  }
  .card--front { left: 378px; top: 75px; width: 476px; height: 303px; }
  .card--back  { left: 376px; top: 417px; width: 477px; height: 310px; }

  .brand {
    position: absolute;
    left: 112px;
    top: 113px;
    height: 76px;
    display: flex;
    align-items: center;
    gap: 22px;
  }
  .brand__dot {
    width: 76px;
    height: 76px;
    border-radius: 50%;
    background: var(--orange);
  }
  .brand__name {
    font-size: 60px;
    font-weight: 500;
    color: var(--ink-soft);
    line-height: 1;
    margin-top: -6px;
  }
  .tagline-rule {
    position: absolute;
    left: 149px;
    top: 252px;
    width: 178px;
    height: 1px;
    background: var(--blue);
  }
  .tagline {
    position: absolute;
    left: 118px;
    top: 257px;
    width: 240px;
    text-align: center;
    font-size: 15px;
    letter-spacing: 0.3px;
    color: var(--blue);
  }

  .badge {
    position: absolute;
    left: 34px;
    top: 31px;
    width: 94px;
    height: 94px;
    border-radius: 50%;
    background: var(--orange);
  }
  .address {
    position: absolute;
    left: 32px;
    top: 227px;
    font-size: 13px;
    line-height: 17.5px;
    color: var(--ink);
  }
  .contact {
    position: absolute;
    left: 267px;
    top: 134px;
    width: 184px;
    color: var(--ink);
  }
  .contact__name {
    font-size: 20px;
    letter-spacing: 0.6px;
    line-height: 26px;
  }
  .contact__role {
    font-size: 14px;
    letter-spacing: 1.2px;
    line-height: 20px;
  }
  .contact__line {
    font-size: 13px;
    line-height: 17.5px;
  }
  .contact__label {
    color: var(--blue);
    display: inline-block;
    width: 16px;
  }
  .contact__rule {
    height: 1px;
    background: var(--blue);
    margin: 5px 0 22px;
  }
  .contact__web { color: var(--blue); }
</style>
</head>
<body>
<main class="stage">
  <section class="card card--front" aria-label="Card front">
    <div class="brand">
      <span class="brand__dot"></span>
      <span class="brand__name">velmo</span>
    </div>
    <div class="tagline-rule"></div>
    <p class="tagline" style="margin:0">E-assessment made easy</p>
  </section>

  <section class="card card--back" aria-label="Card back">
    <span class="badge"></span>
    <address class="address" style="font-style:normal">
      Lindenhofstraat 14<br>
      2517 KM &nbsp;‘S-Gravenhage<br>
      NETHERLANDS
    </address>
    <div class="contact">
      <div class="contact__name">Jonas Verbeek</div>
      <div class="contact__role">MANAGER</div>
      <div class="contact__line"><span class="contact__label">M</span>0150 7314482</div>
      <div class="contact__rule"></div>
      <div class="contact__line"><span class="contact__label">T</span>0655 284 7719</div>
      <div class="contact__line"><span class="contact__label">E</span>verbeek@velmo.nl</div>
      <div class="contact__line contact__web">www.velmo.nl</div>
    </div>
  </section>
</main>
</body>
</html>
```